Wordpress Business Travel Blog and Discussion Board

Oh, Hello!

We are looking for a motivated designer to create a full, turnkey interactive WordPress website geared toward business travel that includes a news style blog (look at ByteHarbor.com and Wirevane.com for the style we like) that is seamlessly integrated with a robust message board (look at GateBanter.com and RoamLedger.com). Ok, so stick with us here because this is actually a pretty cool project that shouldn't be too hard, but yes, of course we have some curve balls that we are throwing your way. Sorry! :)

*On the front page*

- We would like to have a typical news style blog layout that is fun, somewhat professional, and easy to read. That's easy!

- Somewhere within first glance, we would like to have a short list of the most active discussions on our discussion board. (What's trending, or something like that). Not too bad, right?

- Overall, want to have a good amount of content, but we also do not want the visitor to feel as if he or she is having to sift through a lot of content to see what he or she wants to see. Great! We're past the beginning!

We will have traditional visual advertising on all of our pages. Please leave space as necessary :)

*On the Blog/News story pages*

Let's keep these simple - but there is a twist!

Let's say I create a blog/news post. I would like that blog/news post to also be opened as a discussion on the discussion board. For example, I write an article about Coastal Skyways and their service on a particular international flight. This will be opened as a discussion under the Coastal Skyways topic in the discussion board. Other users can also open new discussions under any topic on the discussion board, but they cannot post stories (unless permission is given) to the blog wall. We would like their posts to show up as regular discussion board posts while the news/blog posts by us show up as news/blog posts on the front page, *and* (oh yes we did!) as discussions in the discussion board. Of course, users will still be able to post comments to the news/blog post, which will also be posted in the discussion.

OK, does that make sense? Let me know if I can help make this more clear! :) Sorry!

*Wiki Pages*

Take a look at the Coastal Skyways example above. In that example, my news/blog entry automatically opens a new discussion post. Although we won't necessarily need to create a new wiki page, we would like to tag the post and the discussion to a wiki page about the topic. The wiki page can be created and edited by all users (and locked by us if necessary). BONUS! Can we tag more than one wiki page?

*Websites that inspire us*

ByteHarbor.com - concept and design
Wirevane.com - concept and design
GateBanter.com - concept
RoamLedger.com - concept
pomwhispers.com - concept

All of the sites above are great and we can only thrive with their great success. We are not aiming to be a competitor to the travel sites, but just another great option for interested visitors. Please do not simply copy what they have. What is posted above is a list of our favorite sites that we visit every day.

Our favorite font is Segoe UI, but please don't use this (or a similar font) too much! Maybe just titles would be great. You're the designer so you can make the call here.

Also, our favorite color is blue, but if you have another favorite color, go ahead and show us what you can do! (Don't use too much blue!)

*Oh, and One More Thing*

(I know, you thought we were done. We're not!)

Here's the killer - We would like to create a way for people to, say, enter the details of their next trip and be matched with someone who will also be on a portion of their trip.

For example, let's say I am flying Meridian Airways flight 109 from Los Angeles to New York JFK Airport this Friday. I am staying at the Bellcourt New York Times Square on Friday night, and I am flying back on Saturday night on Kestrel flight 290 from New York JFK airport back to Los Angeles. Another user will also be on the Kestrel flight back to Los Angeles with me and he entered that information in the website. (Note, the user has to manually enter this information). The other user and I will both be notified that there is at least one other user who will be on the same Kestrel flight as me. We will both have the option to reveal our online identity - which will in fact be released to each person as long as each person *mutually* agrees.

This can be very simple - almost like a dating site type of match but it is based on two people being in the same place at the same time (based on what they report). Also, we would like to be able to collect this information - not necessarily tied to the user's true identity. The information we would like to have is - what the user is claiming he or she is doing on the trip (i.e. staying at the Bellcourt Times Square, flying Meridian Airways), and whether or not the user agreed to reveal his or her identity - AND! whether or not the users both revealed their identity.

*Most Important*

HAVE FUN and THANK YOU!! :)

A couple of quick notes - this is a design and code project. We are most likely offering a more $(!) design and code project for the version 2.0 of this website once we get user feedback from this first round.

Also, the name of the website is Jaunta. (www.jaunta-example.com)

Good luck!

Reason: Extending as requested by a few designers. Only 3 more days to get your designs in!

Reason: All designs look great! Last chance for one or two more designers who have requested an extension. All designs that were already submitted on time will be considered with much higher priority. Thank you!

Requirements
Must have
• We need to have a high end, professional, modern, and clean design on the front page to entice readers to constantly visit and stay on our site.
Nice to have
• It would be great to give us the ability to automatically recognize users for visiting the website and/or participating and commenting. Social badges, recognition, etc. would be very cool.
Should not have
• Although this is a website around business travel, we do not necessarily want it to be business travel themed. There can be hints of the theme, but otherwise the visual look should be somewhat generic.

```html
<!DOCTYPE html>
<html lang="en">
<head>
<meta charset="utf-8">
<title>Jaunta – Home</title>
<link href="https://fonts.googleapis.com/css2?family=Ubuntu:wght@400;500;700&family=PT+Sans+Narrow:wght@700&family=Gochi+Hand&display=swap" rel="stylesheet">
<style>
:root{
  --yellow:#ffe600;
  --yellow-deep:#f3d700;
  --blue:#0b5ca8;
  --blue-dark:#084a8a;
  --link:#0a5aa5;
  --accent-yellow:#ffe600;
  --orange:#f08a1c;
  --ink:#333;
  --muted:#555;
  --sky:#e3e3e3;
  --panel:#f0f0f0;
  --line:#c9c9c9;
  --ad-dark:#2b2b2b;
  --pink:#d4217f;
  --cyan:#3aa8dc;
}
*{box-sizing:border-box;margin:0;padding:0}
html,body{width:900px;height:1200px;overflow:hidden;background:#fff}
body{position:relative;font-family:"Ubuntu",sans-serif;color:var(--ink)}
a{text-decoration:none;color:inherit}
.abs{position:absolute}

.topbar{left:0;top:0;width:900px;height:33px;background:linear-gradient(#fff04a,var(--yellow-deep));box-shadow:0 2px 4px rgba(0,0,0,.2);z-index:3}
.topnav{right:98px;top:10px;font-size:10.5px;color:#333;display:flex;gap:6px}
.topnav span.sep{color:#555}
.skyline{left:0;top:33px;width:900px;height:121px;background:linear-gradient(#f4f4f4,#dcdcdc)}
.ground{left:0;top:142px;width:900px;height:12px;background:#d2d2d2}

.brand-disc{left:112px;top:48px;width:148px;height:148px;border-radius:50%;background:var(--blue);border:4px solid #fff;box-shadow:0 2px 6px rgba(0,0,0,.3);display:flex;align-items:center;justify-content:center}
.brand-name{font-family:"Ubuntu",sans-serif;font-weight:700;font-size:28px;color:#fff;letter-spacing:1px}

.my-btn{left:715px;top:44px;width:88px;height:42px;border-radius:50%;background:var(--blue);border:2px solid #fff;box-shadow:0 2px 4px rgba(0,0,0,.35);color:var(--accent-yellow);font-weight:700;font-size:12px;line-height:11px;text-align:center;padding-top:9px}

.forum-nav{left:338px;top:139px;width:464px;height:31px;background:linear-gradient(#fff,#ededed);border:1px solid #d6d6d6;border-radius:3px;box-shadow:0 3px 5px rgba(0,0,0,.15);display:flex;align-items:center;padding-left:10px;font-size:10.5px;color:#333;gap:12px}
.forum-nav .label{color:var(--link)}

.section-head{left:98px;width:464px;height:30px;background:var(--panel);border-radius:3px;font-size:13px;font-weight:500;color:#222;padding:8px 12px}

.post{left:98px;width:464px}
.post .thumb{position:absolute;left:0;top:0;width:190px;height:129px;background:#e3e3e3;border:3px solid #f4f4f4;outline:1px solid #d8d8d8}
.post .date{position:absolute;left:208px;top:1px;width:44px;height:53px;background:var(--blue);color:#fff;font-family:"PT Sans Narrow",sans-serif;font-weight:700;font-size:20px;line-height:22px;text-align:center;padding-top:4px}
.post .comments{position:absolute;left:272px;top:38px;font-size:9px;color:#888;display:flex;align-items:center;gap:7px}
.post h2{position:absolute;left:208px;top:64px;width:240px;font-family:"PT Sans Narrow",sans-serif;font-weight:700;font-size:21px;line-height:22px;color:#333}
.post p{position:absolute;left:0;top:146px;width:464px;font-size:9.2px;line-height:17.3px;color:#444}
.post .more{position:absolute;left:0;top:203px;font-size:9.5px;color:var(--link)}
.post .rule{position:absolute;left:0;top:227px;width:464px;border-top:1px dashed #bbb}

.trend{left:98px;width:464px;height:41px;background:linear-gradient(#fff,#e8e8e8);border-bottom:2px solid #cfcfcf;padding:6px 0 0 33px}
.trend::before{content:"";position:absolute;left:15px;top:9px;width:7px;height:7px;background:var(--yellow)}
.trend h3{font-size:11.5px;font-weight:500;color:var(--link)}
.trend .meta{font-size:8.6px;color:#555;margin-top:2px}
.trend .meta a{color:var(--orange)}

.ad-box{left:578px;top:222px;width:224px;height:187px;background:radial-gradient(circle at 55% 20%,#555,var(--ad-dark) 70%);border:2px solid #999;border-radius:2px;overflow:hidden;color:#fff}
.ribbon{position:absolute;background:var(--pink);color:#fff;font-size:7px;font-weight:700;text-align:center;line-height:8px;transform:rotate(-45deg)}
.hand{font-family:"Gochi Hand",cursive;color:#fff}
.btn-cyan{position:absolute;background:linear-gradient(#5bc3ec,#2f9fd3);border:1px solid #1f86b8;color:#1b3a52;font-size:10px;font-weight:500;text-align:center;border-radius:2px}
.maker{font-weight:700;color:#fff}

.blue-box{left:578px;width:224px;background:var(--blue);border-radius:2px;box-shadow:0 4px 6px rgba(0,0,0,.15);padding:10px 13px}
.blue-box h4{font-size:14px;font-weight:500;color:#fff;margin-bottom:10px}
.blue-box ul{list-style:none}
.blue-box li{position:relative;padding-left:25px;font-size:9.6px;line-height:12.5px;color:var(--accent-yellow)}
.blue-box li::before{content:"";position:absolute;left:0;top:1px;width:10px;height:10px;border-radius:50%;background:var(--cyan)}
.email{width:199px;height:23px;background:#fff;border:1px solid #ccc;border-radius:2px;font-size:10px;color:#777;padding:5px 8px}
.subscribe{display:inline-block;margin-top:14px;background:var(--yellow);color:#222;font-size:11px;padding:3px 10px}
.passport{right:6px;bottom:0;width:68px;height:48px;background:linear-gradient(135deg,#3a4a6a,#8a5a5a);transform:rotate(-8deg);border-radius:3px}

.footer-band{left:0;top:1089px;width:900px;height:111px;background:#f1f1f1;border-top:3px solid var(--yellow)}
.promo{left:178px;top:1049px;width:545px;height:66px;background:radial-gradient(circle at 40% 30%,#555,var(--ad-dark) 70%);border:2px solid #888;overflow:hidden;color:#fff;z-index:2}
.footer-links{left:0;top:1134px;width:900px;text-align:center;font-size:9px;color:var(--link)}
.footer-links span{color:#777;margin:0 4px}
.footer-note{left:0;width:900px;text-align:center;font-size:8px;color:#555}
.footer-note a{color:var(--link)}
</style>
</head>
<body>

<header>
  <div class="abs topbar">
    <nav class="abs topnav">
      <a href="#">Home</a><span class="sep">|</span>
      <a href="#">Blogs</a><span class="sep">|</span>
      <a href="#">Forums</a><span class="sep">|</span>
      <a href="#">Members</a><span class="sep">|</span>
      <a href="#">Extras</a><span class="sep">|</span>
      <a href="#">Help</a>
    </nav>
  </div>
  <div class="abs skyline" role="img" aria-label="Soft grey skyline of world landmarks"></div>
  <div class="abs ground"></div>

  <div class="abs brand-disc"><span class="brand-name">Jaunta</span></div>

  <a href="#" class="abs my-btn">My<br>Jaunta</a>

  <nav class="abs forum-nav">
    <span class="label">Forums:</span>
    <a href="#">Miles &amp; Points</a><span>|</span>
    <a href="#">Travel &amp; Dining</a><span>|</span>
    <a href="#">Community</a><span>|</span>
    <a href="#">Vantage</a><span>|</span>
    <a href="#">Destinations</a>
  </nav>
</header>

<main>
  <div class="abs section-head" style="top:222px">RECENT BLOG</div>

  <article class="abs post" style="top:269px;height:230px">
    <div class="thumb" role="img" aria-label="Blog post photo"></div>
    <div class="date">12<br>SEP</div>
    <div class="comments">
      <svg width="16" height="14" viewBox="0 0 16 14"><rect x="4" y="0" width="12" height="8" rx="2" fill="#1d6fc2"/><rect x="0" y="4" width="11" height="8" rx="2" fill="#4a9ae0"/><path d="M2 12 L2 14 L5 12Z" fill="#4a9ae0"/></svg>
      35 comments
    </div>
    <h2>Orem ipsum dolor sit amet, consectetur adipiscing elit.</h2>
    <p>Aliquam condimentum mi vitae ante pretium vehicula. Pellentesque nec massa et diam tincidunt egestas. Duis porta ultricies lorem sed consectetur. Vestibulum rutrum risus at lectus accumsan euismod. Vivamus sagittis lacus vel augue laoreet rutrum faucibus dolor auctor</p>
    <a href="#" class="more">Read more</a>
    <div class="rule"></div>
  </article>

  <article class="abs post" style="top:525px;height:230px">
    <div class="thumb" role="img" aria-label="Blog post photo"></div>
    <div class="date">10<br>SEP</div>
    <div class="comments">
      <svg width="16" height="14" viewBox="0 0 16 14"><rect x="4" y="0" width="12" height="8" rx="2" fill="#1d6fc2"/><rect x="0" y="4" width="11" height="8" rx="2" fill="#4a9ae0"/><path d="M2 12 L2 14 L5 12Z" fill="#4a9ae0"/></svg>
      15 comments
    </div>
    <h2>Orem ipsum dolor sit amet, consectetur adipiscing elit.</h2>
    <p>Aliquam condimentum mi vitae ante pretium vehicula. Pellentesque nec massa et diam tincidunt egestas. Duis porta ultricies lorem sed consectetur. Vestibulum rutrum risus at lectus accumsan euismod. Vivamus sagittis lacus vel augue laoreet rutrum faucibus dolor auctor</p>
    <a href="#" class="more">Read more</a>
    <div class="rule"></div>
  </article>

  <div class="abs section-head" style="top:778px">WHAT’s TRENDING</div>

  <div class="abs trend" style="top:818px"><h3>Book Your Reservation With Pinecrest Airlines -- Or Else...</h3><div class="meta">Wednesday, September 12, 2012 at 09:24:10 ... <a href="#">Read this article</a></div></div>
  <div class="abs trend" style="top:868px"><h3>Book Your Reservation With Pinecrest Airlines -- Or Else...</h3><div class="meta">Wednesday, September 12, 2012 at 09:24:10 ... <a href="#">Read this article</a></div></div>
  <div class="abs trend" style="top:917px"><h3>Book Your Reservation With Pinecrest Airlines -- Or Else...</h3><div class="meta">Wednesday, September 12, 2012 at 09:24:10 ... <a href="#">Read this article</a></div></div>
  <div class="abs trend" style="top:967px"><h3>Book Your Reservation With Pinecrest Airlines -- Or Else...</h3><div class="meta">Wednesday, September 12, 2012 at 09:24:10 ... <a href="#">Read this article</a></div></div>
</main>

<aside>
  <div class="abs ad-box">
    <div class="ribbon" style="left:-22px;top:20px;width:110px;padding:3px 0">100% Money<br>Back Guarantee</div>
    <div class="abs hand" style="left:56px;top:22px;width:140px;text-align:center;font-size:22px;line-height:30px">Need a graphic designer?</div>
    <div class="btn-cyan" style="left:32px;top:92px;width:158px;height:30px;line-height:28px">BROWSE DESIGNERS</div>
    <div class="abs maker" style="left:0;top:136px;width:220px;text-align:center;font-size:20px">MakerBazaar</div>
    <div class="abs hand" style="left:0;top:161px;width:220px;text-align:center;font-size:12.5px">The #1 Design Marketplace Online</div>
  </div>

  <section class="abs blue-box" style="top:425px;height:161px">
    <h4>Welcome to Jaunta</h4>
    <ul>
      <li style="margin-bottom:11px">New to Jaunta? Please Start Here</li>
      <li style="margin-bottom:11px">Join over 425,376 Members</li>
      <li style="margin-bottom:11px">Read more than 19,007,614 Posts</li>
      <li>Jaunta Members Currently Online: 6,718</li>
    </ul>
  </section>

  <section class="abs blue-box" style="top:602px;height:116px">
    <h4>More Helpful Linkslink</h4>
    <ul>
      <li style="margin-bottom:13px">Guidelines &amp; Rules</li>
      <li style="margin-bottom:13px">Questions? We've got answers</li>
      <li>Airport Information</li>
    </ul>
  </section>

  <section class="abs blue-box" style="top:735px;height:117px;overflow:hidden">
    <h4>Newsletter Sign-Up</h4>
    <div class="email">Enter Email Address</div>
    <span class="subscribe">Subscribe</span>
    <div class="abs passport" role="img" aria-label="Passport with stamps"></div>
  </section>
</aside>

<footer>
  <div class="abs footer-band"></div>
  <div class="abs promo">
    <div class="ribbon" style="left:-20px;top:16px;width:90px;padding:3px 0">100% Money<br>Back Guarantee</div>
    <div class="abs hand" style="left:60px;top:8px;width:190px;text-align:center;font-size:19px">Get 25% off Design</div>
    <div class="abs" style="left:64px;top:38px;width:190px;text-align:center;font-size:11px;color:var(--cyan);font-weight:500">Discount Code: 25-OFF-DISCOUNT</div>
    <div class="btn-cyan" style="left:268px;top:16px;width:102px;height:31px;line-height:29px">START HERE!</div>
    <div class="abs maker" style="left:394px;top:12px;width:140px;text-align:center;font-size:17px">MakerBazaar</div>
    <div class="abs hand" style="left:394px;top:34px;width:140px;text-align:center;font-size:10.5px">The #1 Design Marketplace Online</div>
  </div>
  <div class="abs footer-links">
    <a href="#">Privacy Policy</a><span>|</span><a href="#">Glossary</a><span>|</span><a href="#">Airport Code Lookup</a><span>|</span><a href="#">The Gate</a>
  </div>
  <div class="abs footer-note" style="top:1154px">This site is owned, operated, and maintained by <a href="#">jaunta-example.com</a>. Copyright © 2012 GateBanter.Jaunta.com. All rights reserved.</div>
  <div class="abs footer-note" style="top:1172px">Designated trademarks are the property of their respective owners.</div>
</footer>

</body>
</html>
```